Business card design needed

I would like a one sided black business card with the information provided above. Refer to my website www.brightvolleyracquets.com.au for an example of colors I have used for my site, would like to keep this consistent for my business cards also, I will upload my logo below.

I am a new small business that provides tennis customers with racquet re stringing, tennis strings and accessories.

Industry/Entity Type

Small Business

Contact Information for Business Card

Bright Volley Tennis

Owen Whitby
Managing Director

brightvolleyracquets@mailbox.example
www.brightvolleyracquets.com.au
0491 726 305

Racquet Restringing/Tennis Strings/Accessories

Requirements
Must have
• Must have my logo and card must be black

```html
<!DOCTYPE html>
<html lang="en">
<head>
<meta charset="utf-8">
<title>Bright Volley Tennis – Business Card</title>
<link rel="stylesheet" href="https://fonts.googleapis.com/css2?family=Source+Sans+3:ital,wght@0,400;0,600;0,700;1,700&display=swap">
<style>
  :root {
    --stage: #e9e6e1;
    --card-black: #030506;
    --brand-green: #b6d335;
    --brand-blue: #234f82;
    --text-white: #ffffff;
    --font-body: "Source Sans 3", "Myriad Pro", Arial, sans-serif;
  }
  * { margin: 0; padding: 0; box-sizing: border-box; }
  html, body {
    width: 1200px;
    height: 750px;
    overflow: hidden;
    background: var(--stage);
    font-family: var(--font-body);
  }
  .business-card {
    position: absolute;
    left: 75px;
    top: 75px;
    width: 1050px;
    height: 598px;
    border-radius: 40px;
    overflow: hidden;
    background: var(--card-black);
    color: var(--text-white);
  }
  .card-shapes {
    position: absolute;
    inset: 0;
    width: 100%;
    height: 100%;
  }
  .shape-swoosh { fill: var(--brand-green); }
  .shape-band { fill: var(--brand-blue); }

  .brand-name {
    position: absolute;
    left: 55px;
    top: 128px;
    font-size: 64px;
    font-weight: 700;
    letter-spacing: 0.5px;
    color: var(--brand-green);
    line-height: 1;
    white-space: nowrap;
  }

  .contact-person {
    position: absolute;
    left: 49px;
    top: 343px;
  }
  .person-name {
    font-size: 31px;
    font-weight: 700;
    color: var(--brand-green);
    line-height: 1.1;
  }
  .person-role {
    font-size: 25px;
    font-weight: 400;
    margin-top: 2px;
    line-height: 1.2;
  }
  .contact-line {
    font-size: 25px;
    font-weight: 400;
    line-height: 1.4;
    white-space: nowrap;
  }
  .contact-label {
    font-weight: 700;
    font-style: italic;
  }
  .contact-phone { margin-top: 12px; }

  .contact-online {
    position: absolute;
    left: 49px;
    top: 508px;
  }

  .service-list {
    position: absolute;
    right: 34px;
    top: 465px;
    list-style: none;
    text-align: right;
  }
  .service-item {
    font-size: 25px;
    line-height: 35px;
    white-space: nowrap;
  }
  .service-item::before {
    content: "";
    display: inline-block;
    width: 7px;
    height: 7px;
    background: var(--text-white);
    margin-right: 10px;
    vertical-align: 5px;
  }
</style>
</head>
<body>
  <main class="business-card">
    <svg class="card-shapes" viewBox="0 0 1050 598" aria-hidden="true">
      <path class="shape-swoosh" d="M893,0 L1050,0 L1050,190 C985,300 830,420 630,466 C815,390 935,215 893,0 Z"/>
      <path class="shape-band" d="M0,598 L0,528 C150,482 430,462 640,470 C820,440 970,330 1050,205 L1050,598 Z"/>
    </svg>

    <h1 class="brand-name">Bright Volley Tennis</h1>

    <section class="contact-person">
      <p class="person-name">Owen Whitby</p>
      <p class="person-role">Managing Director</p>
      <p class="contact-line contact-phone"><span class="contact-label">phone</span> 0491 726 305</p>
    </section>

    <section class="contact-online">
      <p class="contact-line"><span class="contact-label">email</span> brightvolleyracquets@mailbox.example</p>
      <p class="contact-line"><span class="contact-label">web</span> www.brightvolleyracquets.com.au</p>
    </section>

    <ul class="service-list">
      <li class="service-item">Racquet Restringing</li>
      <li class="service-item">Tennis Strings</li>
      <li class="service-item">Accessories</li>
    </ul>
  </main>
</body>
</html>
```